Bright Harbor Web Design & Marketing

Will award a 2nd place prize of $100.00 if someone can come up with a logo to match this design!
Updates

Okay, I'm really looking to see some better designs here. What do you think will bring the best designs out? Please remember with all future submissions I'm looking for a cartoon style / illustrator style website. I'm not sure what the technical term is for it, so I uploaded some images in the brief.

Target Market(s)

Small Business Owners

Industry/Entity Type

Marketing

Logo Text

BrightHarbor.com

Number of Pages Required

1 page

Colors

Designer to choose colors to be used in the design.

Requirements
Must have
• Logo should say BrightHarbor.com I would like more than just a text logo. I want some sort of cool custom graphic / icon with it that will look nice on shirts/hats/etc

```html
<!DOCTYPE html>
<html lang="en">
<head>
<meta charset="utf-8">
<title>Bright Harbor Web Design &amp; Marketing</title>
<link href="https://fonts.googleapis.com/css2?family=Cinzel:wght@400;600;700&family=Open+Sans:wght@300;400;600;700&family=Tinos:wght@400;700&display=swap" rel="stylesheet">
<style>
:root{
  --teal:#1fb49a;
  --teal-dark:#14977f;
  --navy:#0c3546;
  --navy-deep:#082a38;
  --hero:#0a5866;
  --orange:#f7881f;
  --ink:#2b2b2b;
  --muted:#555;
  --grey-bg:#f1f1f1;
  --line:#dcdcdc;
  --white:#fff;
}
*{box-sizing:border-box;margin:0;padding:0}
html,body{width:1200px;height:4009px;overflow:hidden}
body{background:var(--white);font-family:"Tinos",serif;color:var(--ink);position:relative}
section,header,footer,nav{position:absolute;left:0;width:1200px}
.abs{position:absolute}
.sans{font-family:"Open Sans",sans-serif}
.heading{font-family:"Cinzel",serif;font-weight:600;color:var(--teal);font-size:34px;letter-spacing:1px;text-align:center}
.heading .lead{color:var(--navy)}
.intro{font-family:"Tinos",serif;font-size:13.5px;line-height:1.6;color:var(--muted);text-align:center;width:900px;left:150px}

/* header */
.site-header{top:0;height:85px;background:var(--white)}
.brand{left:150px;top:18px;display:flex;align-items:center;gap:12px}
.brand-dot{width:44px;height:44px;border-radius:50%;background:var(--teal)}
.brand-name{font-family:"Cinzel",serif;font-weight:700;font-size:30px;color:var(--navy)}
.phone{right:150px;top:26px;display:flex;align-items:center;gap:10px;font-family:"Open Sans",sans-serif;font-weight:600;font-size:26px;color:var(--navy)}
.main-nav{top:85px;height:35px;background:var(--teal);display:flex;padding-left:142px}
.main-nav a{display:block;width:177px;text-align:center;font-family:"Tinos",serif;font-size:15px;color:var(--white);line-height:35px;text-decoration:none;border-right:1px solid rgba(255,255,255,.35);letter-spacing:.5px}
.main-nav a.active{background:var(--navy);width:120px}
.main-nav a:last-child{border-right:none}

/* hero */
.hero{top:120px;height:473px;background:radial-gradient(ellipse at 60% 40%,#117a88 0%,var(--hero) 55%,#073f4b 100%)}
.hero-bulb{left:0;top:10px;width:200px;height:300px;border-radius:50% 50% 40% 40%;background:radial-gradient(circle,#3fa0c0 0%,rgba(10,88,102,0) 70%)}
.hero-devices{left:640px;top:22px;width:490px;height:310px;background:linear-gradient(180deg,#dfe9ee 0%,#9fb6c0 100%);border-radius:12px;opacity:.9}
.hero-title{left:214px;top:60px;font-family:"Open Sans",sans-serif;font-weight:400;color:var(--white);font-size:64px;line-height:1.05;letter-spacing:1px}
.hero-tag{left:0;width:1200px;top:365px;text-align:center;font-family:"Open Sans",sans-serif;font-size:25px;color:var(--white)}
.btn-orange{left:505px;top:410px;width:190px;height:45px;background:var(--orange);color:var(--white);font-family:"Open Sans",sans-serif;font-size:21px;display:flex;align-items:center;justify-content:center;gap:8px}
.slide-arrow{top:225px;width:22px;height:26px;background:#0c2a33;color:#fff;font-size:14px;display:flex;align-items:center;justify-content:center}

/* about */
.about{top:593px;height:310px}
.about h2{left:142px;top:42px;width:530px;white-space:nowrap;font-family:"Cinzel",serif;font-weight:600;font-size:27px;color:var(--teal)}
.about h2 span{color:var(--navy)}
.about p{left:142px;width:515px;font-size:13.5px;line-height:1.65;color:var(--ink)}
.video{left:690px;top:52px;width:380px;height:208px;background:#2d2d2d;border-radius:10px}
.video-screen{left:18px;top:14px;width:344px;height:170px;background:linear-gradient(180deg,#e8ecee,#c8d0d4);display:flex;align-items:center;justify-content:center;gap:10px;font-family:"Tinos",serif;font-weight:700;font-size:24px;color:var(--navy)}
.play{width:40px;height:40px;border-radius:50%;background:#222;display:flex;align-items:center;justify-content:center}

/* services */
.services{top:903px;height:554px;background:var(--grey-bg)}
.svc-menu{left:142px;top:187px;width:248px}
.svc-menu li{list-style:none;height:32px;margin-bottom:1.5px;background:var(--navy);color:var(--white);font-family:"Open Sans",sans-serif;font-size:12px;display:flex;align-items:center;gap:8px;padding-left:10px}
.svc-menu li.active{background:var(--teal)}
.svc-menu li i{width:14px;height:12px;border:1.5px solid #fff;border-radius:2px}
.svc-icon{left:414px;top:225px;width:125px;height:110px}
.svc-detail{left:556px;top:210px;width:560px}
.svc-detail h3{font-family:"Open Sans",sans-serif;font-weight:700;font-size:16px;color:var(--navy);text-decoration:underline;margin-bottom:12px}
.svc-detail li{list-style:none;display:flex;gap:10px;font-size:12.5px;line-height:1.4;color:var(--ink);margin-bottom:12px}
.svc-detail li b{flex:none;width:14px;height:14px;background:var(--navy);color:#fff;font-size:10px;display:flex;align-items:center;justify-content:center;margin-top:1px}
.answers{left:575px;top:373px;font-family:"Cinzel",serif;font-weight:600;font-size:22px;color:var(--teal)}
.btn-pill{height:28px;background:var(--navy);color:#fff;font-family:"Open Sans",sans-serif;font-weight:600;font-size:14px;border-radius:0 14px 14px 0;display:flex;align-items:center;gap:8px;padding:0 18px 0 10px}
.btn-pill .leaf{width:16px;height:16px;border-radius:50%;background:var(--teal)}

/* cta */
.cta{top:1457px;height:222px}
.cta h2{top:52px;left:0;width:1200px;text-align:center;font-family:"Cinzel",serif;font-weight:700;font-size:34px;color:var(--teal)}
.cta p{top:96px;left:150px;width:900px;text-align:center;font-family:"Open Sans",sans-serif;font-weight:600;font-size:19px;line-height:1.45;color:var(--navy-deep)}

/* pricing */
.pricing{top:1679px;height:660px;background:repeating-linear-gradient(90deg,#0c3c50 0 3px,#0e4357 3px 6px)}
.pricing .heading{top:40px;left:0;width:1200px;color:var(--white)}
.wood{left:0;top:480px;width:1200px;height:180px;background:linear-gradient(180deg,#c79563,#a8703f)}
.plan{width:206px;height:460px;background:var(--white);border-top:5px solid var(--teal);box-shadow:0 8px 14px rgba(0,0,0,.35);text-align:center}
.plan-icon{margin:22px auto 0;width:54px;height:54px;border-radius:50%;border:2px solid var(--teal);display:flex;align-items:center;justify-content:center}
.plan-icon span{width:24px;height:24px;border-radius:50%;background:var(--navy)}
.plan h3{font-family:"Open Sans",sans-serif;font-weight:600;font-size:17px;color:var(--navy);margin-top:26px}
.plan .from{font-size:12px;color:#777;margin-top:16px}
.plan .price{font-family:"Open Sans",sans-serif;font-size:38px;color:var(--navy);line-height:1.1}
.plan .price sup,.plan .price small{font-size:16px}
.plan ul{text-align:left;margin:16px 0 0 24px;background:#fbf7f1}
.plan li{list-style:none;font-size:11.5px;color:#444;line-height:26px}
.plan li::before{content:"›";margin-right:8px;color:var(--navy)}
.plan .btn{margin:22px auto 0;width:118px;height:28px;color:#fff;font-family:"Open Sans",sans-serif;font-size:13px;display:flex;align-items:center;justify-content:center;gap:14px}
.plan .more{font-family:"Open Sans",sans-serif;font-size:11px;color:#444;margin-top:8px}
.plan .more::after{content:"";display:inline-block;width:8px;height:8px;border:1.5px solid var(--teal);margin-left:30px}

/* clients */
.clients{top:2339px;height:254px}
.clients .heading{top:40px;left:0;width:1200px}
.client-row{left:147px;top:190px;width:910px;display:flex;justify-content:space-between;align-items:center}
.client{display:flex;align-items:center;gap:6px;font-family:"Open Sans",sans-serif;font-weight:700;font-size:17px;color:#1d1d1d}
.client i{width:14px;height:14px;border-radius:50%;background:#1d1d1d}
.chev{top:192px;color:#999;font-size:26px;font-family:"Open Sans",sans-serif}

/* why */
.why{top:2593px;height:494px;background:var(--grey-bg)}
.why .heading{top:40px;left:0;width:1200px}
.feature{top:148px;width:165px;height:148px;background:var(--white);box-shadow:0 3px 6px rgba(0,0,0,.12);text-align:center}
.feature .ic{margin:20px auto 0;width:70px;height:62px;background:linear-gradient(180deg,#1fb49a,#0c3546);border-radius:10px}
.feature p{font-family:"Open Sans",sans-serif;font-size:11px;color:#222;margin-top:12px;line-height:1.3}
.panel{left:147px;top:334px;width:895px;height:147px;background:var(--white);box-shadow:0 3px 6px rgba(0,0,0,.12)}
.panel h4{background:#e7eef0;font-family:"Open Sans",sans-serif;font-weight:600;font-size:15px;color:var(--navy);padding:6px 14px}
.panel p{font-size:13px;line-height:1.7;color:#333;padding:6px 14px 0}

/* team */
.team{top:3087px;height:361px}
.team .heading{top:46px;left:0;width:1200px}
.member{top:166px;width:422px;height:142px;border:1px solid var(--line);background:var(--white)}
.member .photo{left:14px;top:12px;width:68px;height:68px;background:linear-gradient(180deg,#b8c2c8,#6e7d86)}
.member h4{left:100px;top:26px;font-family:"Open Sans",sans-serif;font-weight:700;font-size:15px;color:var(--navy)}
.member .role{left:100px;top:47px;font-family:"Open Sans",sans-serif;font-size:12px;color:var(--teal)}
.member p{left:14px;top:92px;width:395px;font-size:12px;line-height:1.45;color:#333}

/* inquiry */
.inquiry{top:3448px;height:414px;background:linear-gradient(90deg,#e9eef0 0%,#fafafa 45%,#fff 100%)}
.inquiry-photo{left:0;top:10px;width:468px;height:404px;background:linear-gradient(160deg,#f4f6f7 0%,#cfd6da 60%,#9aa6ad 100%)}
.dots{left:498px;top:8px;display:flex;gap:12px}
.dots span{width:34px;height:34px;background:var(--navy)}
.dots span.on{background:var(--teal)}
.inquiry h2{left:487px;top:62px;font-family:"Cinzel",serif;font-weight:600;font-size:34px;color:var(--teal)}
.inquiry h2 span{color:var(--navy)}
.field{font-family:"Open Sans",sans-serif;font-size:10.5px;color:#555;border-bottom:1px solid #bbb;height:26px;width:260px;padding-top:4px}
.area{left:489px;top:240px;width:526px;height:90px;border:1px solid #bbb;font-family:"Open Sans",sans-serif;font-size:10.5px;color:#555;padding:6px 6px}
.submit{left:489px;top:340px;width:86px;height:29px;background:var(--teal);color:#fff;font-family:"Open Sans",sans-serif;font-weight:700;font-size:11px;display:flex;align-items:center;justify-content:center}

/* footer */
.site-footer{top:3862px;height:147px;background:var(--navy)}
.f-item{top:38px;display:flex;align-items:flex-start;gap:14px;font-family:"Open Sans",sans-serif;font-size:11.5px;color:#fff;line-height:1.45}
.f-item b{font-weight:700}
.f-ring{width:50px;height:50px;border-radius:50%;border:2px solid var(--teal);display:flex;align-items:center;justify-content:center;flex:none}
.copy{left:225px;top:116px;font-family:"Open Sans",sans-serif;font-size:10.5px;color:#d5dde0}
.socials{left:882px;top:109px;display:flex;gap:9px}
.socials span{width:22px;height:22px;border-radius:50%;border:1.5px solid #9fb3bb}
</style>
</head>
<body>

<header class="site-header">
  <div class="abs brand"><span class="brand-dot"></span><span class="brand-name">Bright Harbor Web Design</span></div>
  <div class="abs phone">
    <svg width="28" height="28" viewBox="0 0 28 28"><circle cx="14" cy="14" r="12.5" fill="none" stroke="#1fb49a" stroke-width="2"/><path d="M10 8c1 0 2 2.5 2 3s-1.5 1-1 2 2.5 3.5 4 4 1-1 2-1 3 1 3 2-1.5 2.5-3 2.2C12 19.5 8.5 16 8 12c-.2-2 1-4 2-4z" fill="#1fb49a"/></svg>
    123-456-7890
  </div>
</header>

<nav class="main-nav">
  <a class="active" href="#">HOME</a>
  <a href="#">SERVICES &amp; PRICING</a>
  <a href="#">OUR TEAM</a>
  <a href="#">CLIENTS</a>
  <a href="#">CONTACT US</a>
</nav>

<section class="hero">
  <div class="abs hero-bulb" role="img" aria-label="Light bulb illustration surrounded by web and social icons"></div>
  <div class="abs hero-devices" role="img" aria-label="Illustration of desktop, laptop, tablet and phone showing websites"></div>
  <div class="abs hero-title">COMPLETE<br>WEB Solution</div>
  <div class="abs slide-arrow" style="left:0">‹</div>
  <div class="abs slide-arrow" style="right:0">›</div>
  <div class="abs hero-tag">The Design &amp; Marketing Team That Always Puts Trust &amp; Loyalty Before Profits</div>
  <div class="abs btn-orange">
    <svg width="22" height="22" viewBox="0 0 22 22"><path d="M6 3c1.5 0 3 3.5 3 4s-2 1.5-1.5 3 3.5 5 5.5 5.5 1.5-1.5 3-1.5 4 1.5 4 3-2 3.5-4 3C8 19 3 13 3 7.5 3 5 4.5 3 6 3z" fill="#fff"/></svg>
    Call Us Today
  </div>
</section>

<section class="about">
  <h2 class="abs">About <span>Bright Harbor Web Design</span></h2>
  <p class="abs" style="top:102px">We believe that honesty and integrity come before personal profits. We are a family owned and operated company. Our parents raised us to take care of each other and that's exactly what we've done. We treat each of our clients with the same loyalty and respect that we give each other.</p>
  <p class="abs" style="top:200px">We are not looking to have hundreds and hundreds of clients. We are looking to expand our family with a handful of like-minded individuals. Companies who take pride in their work and their customers. We want to build mutually beneficial, lucrative, and long term partnerships.</p>
  <div class="abs video">
    <div class="abs video-screen">Bright Harbor <span class="play"><svg width="14" height="16" viewBox="0 0 14 16"><path d="M2 1l11 7-11 7z" fill="#fff"/></svg></span> Web Design</div>
  </div>
</section>

<section class="services">
  <h2 class="abs heading" style="top:60px;left:0;width:1200px"><span class="lead">Services</span> We Provide</h2>
  <p class="abs intro" style="top:108px">Lorem ipsum dolor sit amet, consectetuer adipiscing elit, sed diam nonummy nibh euismod tincidunt ut laoreet dolore magna aliquam erat volutpat. Ut wisi enim ad minim veniam, quis nostrud exerci.</p>
  <ul class="abs svc-menu">
    <li class="active"><i></i>Website Design &amp; Management</li>
    <li><i></i>Logo Design &amp; Branding Materials</li>
    <li><i></i>Online Store Design &amp; Management</li>
    <li><i></i>Local Seo Management</li>
    <li><i></i>Search Engine Optimization</li>
    <li><i></i>Social Media Marketing</li>
    <li><i></i>Marketing Material &amp; Print Design</li>
    <li><i></i>Outsourcing Management</li>
    <li><i></i>Consulting Service</li>
  </ul>
  <svg class="abs svc-icon" viewBox="0 0 125 110" role="img" aria-label="Monitor with pen icon">
    <rect x="6" y="22" width="92" height="62" fill="none" stroke="#555" stroke-width="6"/>
    <rect x="40" y="84" width="24" height="12" fill="#555"/><rect x="28" y="96" width="48" height="6" fill="#555"/>
    <path d="M112 6l8 8-52 52-12 4 4-12z" fill="#555"/>
  </svg>
  <div class="abs svc-detail">
    <h3>Website Design &amp; Management</h3>
    <ul>
      <li><b>✓</b>Lorem dolor sit amet, consectetuer adipiscing elit, sed diam nonummy nibh euismod</li>
      <li><b>✓</b>Lorem dolor sit amet, consectetuer adipiscing</li>
      <li><b>✓</b>Lorem dolor sit amet, consectetuer adipiscing elit, sed diam nonummy nibh euismod</li>
      <li><b>✓</b>Lorem dolor sit amet, consectetuer adipiscing elit, sed diam nonummy nibh<br>euismod.onsenonummy dolor sit amet.</li>
    </ul>
  </div>
  <div class="abs answers">We Have Answers</div>
  <div class="abs btn-pill" style="left:556px;top:411px;width:302px"><span class="leaf"></span>Call Us Today To Avail The Service</div>
</section>

<section class="cta">
  <h2 class="abs">Lorem Ipsum Dolor Sit Amet Consectetuer</h2>
  <p class="abs">Lorem ipsum dolor sit amet consectetuer&nbsp; adipiscing elit sed diam the nonummy nibh sit amet consectetuer adipiscing elit sed consectetuer.</p>
  <div class="abs btn-pill" style="left:517px;top:158px;width:166px"><span class="leaf"></span>Call Us Today</div>
</section>

<section class="pricing">
  <h2 class="abs heading">Our&nbsp; Pricing</h2>
  <div class="abs wood" role="img" aria-label="Wooden floor"></div>
  <div class="abs plan" style="left:160px;top:146px">
    <div class="plan-icon"><span></span></div><h3>Basic Plan</h3>
    <div class="from">Starting from</div><div class="price"><sup>$</sup>52.<small>95</small></div>
    <ul><li>Lorem Ipsum Dolor Ipsum</li><li>Lorem Ipsum Dolor</li><li>Lorem Ipsum Dolor Ipsum</li><li>Lorem Ipsum Dolor</li></ul>
    <div class="btn" style="background:var(--navy-deep)">Get Started <span>→</span></div><div class="more">More Information</div>
  </div>
  <div class="abs plan" style="left:396px;top:133px">
    <div class="plan-icon"><span></span></div><h3>Standard Plan</h3>
    <div class="from">Starting from</div><div class="price"><sup>$</sup>114.<small>00</small></div>
    <ul><li>Lorem Ipsum Dolor Ipsum</li><li>Lorem Ipsum Dolor</li><li>Lorem Ipsum Dolor Ipsum</li><li>Lorem Ipsum Dolor</li></ul>
    <div class="btn" style="background:var(--teal)">Get Started <span>→</span></div><div class="more">More Information</div>
  </div>
  <div class="abs plan" style="left:623px;top:146px">
    <div class="plan-icon" style="border-color:var(--orange)"><span style="background:var(--orange)"></span></div><h3>Gold Plan</h3>
    <div class="from">Starting from</div><div class="price"><sup>$</sup>200.<small>95</small></div>
    <ul><li>Lorem Ipsum Dolor Ipsum</li><li>Lorem Ipsum Dolor</li><li>Lorem Ipsum Dolor Ipsum</li><li>Lorem Ipsum Dolor</li></ul>
    <div class="btn" style="background:var(--teal)">Get Started <span>→</span></div><div class="more">More Information</div>
  </div>
  <div class="abs plan" style="left:855px;top:146px">
    <div class="plan-icon"><span style="background:#9fb3bb"></span></div><h3>Platinum Plan</h3>
    <div class="from">Starting from</div><div class="price"><sup>$</sup>490.<small>00</small></div>
    <ul><li>Lorem Ipsum Dolor Ipsum</li><li>Lorem Ipsum Dolor</li><li>Lorem Ipsum Dolor Ipsum</li><li>Lorem Ipsum Dolor</li></ul>
    <div class="btn" style="background:var(--teal)">Get Started <span>→</span></div><div class="more">More Information</div>
  </div>
</section>

<section class="clients">
  <h2 class="abs heading"><span class="lead">Our</span> Valuable Clients</h2>
  <p class="abs intro" style="top:96px">Lorem ipsum dolor sit amet, consectetuer adipiscing elit, sed diam nonummy nibh euismod tincidunt ut laoreet dolore magna aliquam erat volutpat. Ut wisi enim ad minim veniam, quis nostrud exerci.</p>
  <div class="abs chev" style="left:108px">‹</div>
  <div class="abs client-row">
    <div class="client"><i></i>Kestrel</div>
    <div class="client"><i></i>Northwind</div>
    <div class="client"><i></i>Northwind</div>
    <div class="client">Lumen</div>
    <div class="client"><i></i>Kestrel</div>
    <div class="client"><i></i>Orbitra</div>
    <div class="client">Arcway</div>
    <div class="client">Arcway</div>
  </div>
  <div class="abs chev" style="left:1072px">›</div>
</section>

<section class="why">
  <h2 class="abs heading"><span class="lead">Why</span> Choose Us</h2>
  <p class="abs intro" style="top:96px">Lorem ipsum dolor sit amet, consectetuer adipiscing elit, sed diam nonummy nibh euismod tincidunt ut laoreet dolore magna aliquam erat volutpat. Ut wisi enim ad minim veniam, quis nostrud exerci.</p>
  <div class="abs feature" style="left:155px"><div class="ic" role="img" aria-label="Hand holding coin icon"></div><p>100% Risk Free<br>Investment</p></div>
  <div class="abs feature" style="left:342px"><div class="ic" role="img" aria-label="Loyalty card icon"></div><p>Customer Loyalty<br>Program</p></div>
  <div class="abs feature" style="left:530px"><div class="ic" role="img" aria-label="24/7 support clock icon"></div><p>24/7 U.S Based<br>Customer Support</p></div>
  <div class="abs feature" style="left:705px"><div class="ic" role="img" aria-label="Personal service icon"></div><p>Unmatched Personal<br>Service</p></div>
  <div class="abs feature" style="left:890px"><div class="ic" role="img" aria-label="Payment options icon"></div><p>Multiple Payment<br>Options Available</p></div>
  <svg class="abs" style="left:760px;top:318px" width="20" height="16"><path d="M0 16L10 4 20 16z" fill="#fff"/></svg>
  <div class="abs panel">
    <h4>Unmatched Personal Service</h4>
    <p>Do you need us to come to your office to help train staff on the management of your new website, content management system, or computer software?<br>That's not a problem.<br>We welcome to you and provide hands on training.</p>
  </div>
</section>

<section class="team">
  <h2 class="abs heading"><span class="lead">Our</span> Team</h2>
  <p class="abs intro" style="top:104px">Lorem ipsum dolor sit amet, consectetuer adipiscing elit, sed diam nonummy nibh euismod tincidunt ut laoreet dolore magna aliquam erat volutpat. Ut wisi enim ad minim veniam, quis nostrud exerci.</p>
  <div class="abs chev" style="left:112px;top:220px">‹</div>
  <div class="abs member" style="left:147px">
    <div class="abs photo" role="img" aria-label="Portrait photo of team member"></div>
    <h4 class="abs">DANIEL HARTLEY</h4><div class="abs role">Chief Executive Officer</div>
    <p class="abs">Lorem ipsum dolor sit amet, consectetuer adipiscing elit, sed diam nonummy nibh euismod tincidunt ut laoreet dolore magna aliquam erat...[+]</p>
  </div>
  <div class="abs member" style="left:628px">
    <div class="abs photo" role="img" aria-label="Portrait photo of team member"></div>
    <h4 class="abs">OWEN PRESCOTT</h4><div class="abs role">Chief Operations Officer</div>
    <p class="abs">Lorem ipsum dolor sit amet, consectetuer adipiscing elit, sed diam nonummy nibh euismod tincidunt ut laoreet dolore magna aliquam erat...[+]</p>
  </div>
  <div class="abs chev" style="left:1070px;top:220px">›</div>
</section>

<section class="inquiry">
  <div class="abs inquiry-photo" role="img" aria-label="Photo of hands typing on a laptop on a white desk with a plant and coffee cup"></div>
  <div class="abs dots"><span></span><span class="on"></span></div>
  <h2 class="abs"><span>Quick</span> Inquiry</h2>
  <div class="abs field" style="left:489px;top:116px">First Name</div>
  <div class="abs field" style="left:765px;top:116px;width:250px">Last Name</div>
  <div class="abs field" style="left:489px;top:166px">Email</div>
  <div class="abs field" style="left:765px;top:166px;width:250px">Phone Number</div>
  <div class="abs sans" style="left:493px;top:218px;font-size:10.5px;color:#555">Details About Your Enquiry</div>
  <div class="abs area"></div>
  <div class="abs submit">SUBMIT</div>
</section>

<footer class="site-footer">
  <div class="abs f-item" style="left:214px">
    <span class="f-ring"><svg width="18" height="24" viewBox="0 0 18 24"><path d="M9 1a8 8 0 00-8 8c0 6 8 14 8 14s8-8 8-14a8 8 0 00-8-8zm0 11a3 3 0 110-6 3 3 0 010 6z" fill="#fff"/></svg></span>
    <div><b>BRIGHT HARBOR Web Design</b><br>Street Name, City Name<br>State Zip code</div>
  </div>
  <div class="abs f-item" style="left:529px">
    <span class="f-ring"><svg width="20" height="20" viewBox="0 0 22 22"><path d="M6 3c1.5 0 3 3.5 3 4s-2 1.5-1.5 3 3.5 5 5.5 5.5 1.5-1.5 3-1.5 4 1.5 4 3-2 3.5-4 3C8 19 3 13 3 7.5 3 5 4.5 3 6 3z" fill="#fff"/></svg></span>
    <div><b>Phone:</b><br>+012 3456 789</div>
  </div>
  <div class="abs f-item" style="left:794px">
    <span class="f-ring"><svg width="22" height="16" viewBox="0 0 22 16"><rect x="1" y="1" width="20" height="14" fill="none" stroke="#fff" stroke-width="2"/><path d="M1 1l10 8 10-8" fill="none" stroke="#fff" stroke-width="2"/></svg></span>
    <div><b>Email:</b><br>inquiry@brightharbor.com</div>
  </div>
  <div class="abs copy">Copyright © 2017 BRIGHT HARBOR WEB DESIGN. All Rights Reserved.</div>
  <div class="abs socials"><span></span><span></span><span></span><span></span><span></span></div>
</footer>

</body>
</html>
```